Simple landing page for Brambles cookbook

I need a one page landingpage where customers can order the cookbook.
This is a cookbook of a collection of recipes from our deli that we used to run.
I need a landing page where customers can come and order the book. I also need it coded. I already have the domain through hostwell.
I can send the file of the book through wetransfer. It's too big to upload here. Just so you get the feel that I am looking for.
I attached a simple text as an introduction to the page. But I am open to any suggestions. I want it all to be about the experience that we are sharing the recipes with everybody and that it's for sale. The book is $29.99, shipping included.
Customers have to be able to click and buy the book from it.

Coding

Coded - Design and coding required

Number of Pages Required

1 page

Font styles to use
Sans Serif

Requirements
Must have
• Same colors as the cookbook

```html
<!DOCTYPE html>
<html lang="en">
<head>
<meta charset="utf-8">
<title>Brambles Sandwiches – The Cookbook</title>
<link rel="stylesheet" href="https://fonts.googleapis.com/css2?family=Fjalla+One&family=Quicksand:wght@500;600;700&display=swap">
<style>
  :root{
    --brown:#4a2a1c;
    --crimson:#c2194f;
    --sky:#c6def0;
    --sky-soft:#e3eff8;
    --sky-deep:#2b6c9c;
    --white:#ffffff;
    --olive:#7f9a3a;
    --text:#2b2522;
  }
  *{margin:0;padding:0;box-sizing:border-box}
  html,body{width:1200px;height:2367px;overflow:hidden;background:var(--white)}
  body{position:relative;font-family:"Quicksand",sans-serif;color:var(--text)}
  .waves{position:absolute;left:0;top:0;width:1200px;height:2367px}
  .abs{position:absolute}

  .brand{font-family:"Fjalla One",sans-serif;color:var(--brown);font-size:42px;line-height:1;letter-spacing:.5px;display:flex;align-items:center;gap:10px}
  .brand-dot{width:12px;height:12px;border-radius:50%;background:var(--crimson)}

  .hero-title{left:145px;top:205px;width:520px;font-family:"Fjalla One",sans-serif;font-size:37px;line-height:51px;color:var(--brown);text-transform:uppercase;letter-spacing:1px}
  .includes{left:145px;top:378px;font-size:17px;font-weight:700;letter-spacing:1.5px;color:var(--brown);text-transform:uppercase}
  .includes strong{color:var(--crimson);font-size:23px;letter-spacing:1.5px}
  .categories{left:145px;top:416px;display:flex;gap:30px;font-size:14px;font-weight:600;letter-spacing:1px;color:var(--brown)}
  .categories span{display:flex;align-items:center;gap:8px}

  .btn{display:flex;align-items:center;justify-content:center;background:var(--crimson);color:var(--white);font-family:"Fjalla One",sans-serif;font-size:17px;letter-spacing:2px;border-radius:20px;text-decoration:none;text-transform:uppercase}
  .btn-hero{left:145px;top:467px;width:152px;height:37px}
  .btn-buy{left:772px;top:1645px;width:152px;height:37px}

  .book-cover{left:724px;top:50px;width:318px;height:480px;border-radius:6px 14px 14px 6px;background:linear-gradient(180deg,#eef4fa 0%,#d9e6f1 35%,#c48a4f 60%,#5a8a3a 72%,#b06a32 85%,#e8eef3 100%);box-shadow:14px 10px 0 -2px #c9ccd1,20px 30px 40px rgba(60,90,120,.25)}

  .price{width:136px;height:136px}
  .price-hero{left:653px;top:130px}
  .price-offer{left:794px;top:1350px;width:106px;height:106px}

  .sandwich-photo{left:144px;top:680px;width:912px;height:545px;border-radius:0 0 30px 30px;background:radial-gradient(ellipse at 60% 55%,#d98a54 0%,#c9584a 25%,#b47d6b 45%,#6a9a3e 62%,#4a4440 85%,#3a3532 100%);-webkit-mask-image:linear-gradient(180deg,transparent 0,#000 120px);mask-image:linear-gradient(180deg,transparent 0,#000 120px)}
  .stamp{left:75px;top:862px;width:276px;height:276px;border-radius:50%;background:var(--white);border:4px solid var(--olive)}

  .books-photo{left:0;top:1342px;width:666px;height:432px;background:linear-gradient(150deg,transparent 8%,#b9cedf 20%,#dfe9f2 35%,#c38c55 55%,#6b9a45 65%,#b9cedf 80%,transparent 92%);clip-path:polygon(0 48%,20% 38%,38% 20%,57% 12%,98% 47%,60% 96%,35% 78%,22% 88%,0 62%)}

  .offer-title{left:600px;top:1470px;width:494px;text-align:center;font-family:"Fjalla One",sans-serif;font-size:46px;line-height:53px;color:var(--brown);letter-spacing:3px;text-transform:uppercase}
  .offer-text{left:600px;top:1583px;width:494px;text-align:center;font-size:14px;font-weight:600;line-height:19px;letter-spacing:1px;color:var(--brown)}

  .pretzel-photo{left:0;top:1792px;width:1200px;height:503px;background:radial-gradient(ellipse 32% 48% at 62% 42%,#c98d4d 0%,#d9a868 45%,rgba(236,214,182,.6) 75%,transparent 100%),linear-gradient(180deg,#fff 0%,#f1ece6 50%,#fff 100%)}
  .footer-brand{left:145px;top:1930px}

  .quote{left:147px;top:2063px;width:870px;height:170px;border:4px solid var(--sky-deep);border-right:none;border-radius:14px 0 0 14px;-webkit-mask-image:linear-gradient(90deg,#000 75%,transparent 100%);mask-image:linear-gradient(90deg,#000 75%,transparent 100%)}
  .quote-mark{left:158px;top:2031px;width:60px;height:60px;border-radius:50%;background:var(--crimson);color:var(--white);font-family:"Fjalla One",sans-serif;font-size:52px;line-height:80px;text-align:center}
  .quote-text{left:177px;top:2102px;width:680px;font-size:19px;font-weight:600;line-height:30px;letter-spacing:1.4px;color:var(--text)}

  .site-footer{left:0;top:2295px;width:1200px;height:72px;background:linear-gradient(90deg,#2c6a99,#3581b5);color:#e8f1f8;font-size:14px;font-weight:600;display:flex;align-items:center;justify-content:center;letter-spacing:.3px}
</style>
</head>
<body>

<svg class="waves" viewBox="0 0 1200 2367" aria-hidden="true">
  <path d="M0 220 C200 120 500 110 700 170 C900 230 1050 290 1200 260 L1200 0 L0 0 Z" fill="var(--sky-soft)" opacity=".55"/>
  <path d="M0 225 C180 150 420 130 620 160 C800 190 860 260 760 330 C620 430 300 400 0 400 Z" fill="var(--sky)" opacity=".7"/>
  <path d="M80 220 C250 150 450 120 650 150" stroke="#fff" stroke-width="4" fill="none" opacity=".8"/>
  <path d="M1200 170 C1120 250 1060 300 990 330 L1200 330 Z" fill="var(--sky)" opacity=".6"/>
  <path d="M0 1150 C120 1200 200 1230 260 1250 C180 1250 90 1245 0 1240 Z" fill="var(--sky)" opacity=".8"/>
  <path d="M0 1420 C300 1360 700 1420 1000 1330 C1100 1300 1160 1290 1200 1285 L1200 1760 L920 1760 C700 1720 400 1650 0 1650 Z" fill="var(--sky)"/>
  <path d="M600 1410 C800 1400 1000 1370 1200 1300 L1200 1380 C1000 1420 800 1420 600 1410 Z" fill="var(--sky-soft)" opacity=".7"/>
</svg>

<div class="abs brand" style="left:145px;top:38px"><span class="brand-dot"></span>Brambles</div>

<h1 class="abs hero-title">It's finally here! The Brambles cookbook with all your favourite recipes</h1>
<p class="abs includes">Book includes <strong>28 Recipes</strong>:</p>
<div class="abs categories">
  <span><svg width="20" height="16" viewBox="0 0 20 16"><path d="M2 10 L10 3 L18 10 Z M2 12 H18 M2 14 H18" stroke="var(--olive)" stroke-width="1.4" fill="none"/></svg>Sandwiches</span>
  <span><svg width="20" height="16" viewBox="0 0 20 16"><path d="M2 6 H18 C17 11 14 13 10 13 C6 13 3 11 2 6 Z M14 6 L18 2" stroke="var(--olive)" stroke-width="1.4" fill="none"/></svg>Sauces</span>
  <span><svg width="22" height="18" viewBox="0 0 22 18"><path d="M3 9 C3 4 19 4 19 9 Z M3 12 H19 M4 15 H18 M11 1 V3 M6 2 L7 4 M16 2 L15 4" stroke="var(--olive)" stroke-width="1.4" fill="none"/></svg>Burgers</span>
</div>
<a class="abs btn btn-hero" href="#order">Order now</a>

<div class="abs book-cover" role="img" aria-label="Cookbook cover showing a ham and cheese sandwich on a plate"></div>

<svg class="abs price price-hero" viewBox="0 0 136 136" aria-label="$29.99 free shipping">
  <polygon fill="var(--crimson)" points="68,4 82,14 99,11 106,27 122,34 120,51 132,64 122,78 125,95 109,102 102,118 85,116 68,128 54,116 36,120 30,103 14,96 16,79 4,66 16,52 13,35 29,28 36,12 53,15"/>
  <text x="66" y="75" text-anchor="middle" font-family="Fjalla One, sans-serif" font-size="38" fill="#fff"><tspan font-size="20">$</tspan>29.99</text>
  <g stroke="#fff" stroke-width="1.4" fill="none"><rect x="34" y="84" width="14" height="10"/><path d="M48 87 H54 L57 91 V94 H48"/><circle cx="38" cy="96" r="2"/><circle cx="53" cy="96" r="2"/></g>
  <text x="62" y="90" font-family="Quicksand, sans-serif" font-weight="600" font-size="11" fill="#fff">Free</text>
  <text x="62" y="102" font-family="Quicksand, sans-serif" font-weight="600" font-size="11" fill="#fff">Shipping</text>
</svg>

<div class="abs sandwich-photo" role="img" aria-label="Close-up photo of a baguette sandwich with ham, cheese, peppers and lettuce on a wooden table"></div>
<div class="abs stamp" role="img" aria-label="Round fresh and tasty stamp"></div>

<div class="abs books-photo" role="img" aria-label="Two copies of the cookbook lying at an angle"></div>

<svg class="abs price price-offer" viewBox="0 0 136 136" aria-label="$29.99 free shipping">
  <polygon fill="var(--crimson)" points="68,4 82,14 99,11 106,27 122,34 120,51 132,64 122,78 125,95 109,102 102,118 85,116 68,128 54,116 36,120 30,103 14,96 16,79 4,66 16,52 13,35 29,28 36,12 53,15"/>
  <text x="66" y="75" text-anchor="middle" font-family="Fjalla One, sans-serif" font-size="38" fill="#fff"><tspan font-size="20">$</tspan>29.99</text>
  <g stroke="#fff" stroke-width="1.4" fill="none"><rect x="34" y="84" width="14" height="10"/><path d="M48 87 H54 L57 91 V94 H48"/><circle cx="38" cy="96" r="2"/><circle cx="53" cy="96" r="2"/></g>
  <text x="62" y="90" font-family="Quicksand, sans-serif" font-weight="600" font-size="11" fill="#fff">Free</text>
  <text x="62" y="102" font-family="Quicksand, sans-serif" font-weight="600" font-size="11" fill="#fff">Shipping</text>
</svg>

<h2 class="abs offer-title">Favorite recipes<br>in one book</h2>
<p class="abs offer-text">We Truly Hope You Will Enjoy Making These<br>Sandwiches Just As Much As We Did.</p>
<a class="abs btn btn-buy" id="order" href="#order">Byu now</a>

<div class="abs pretzel-photo" role="img" aria-label="Soft-focus photo of a salted pretzel sandwich on a white plate"></div>
<div class="abs brand footer-brand"><span class="brand-dot"></span>Brambles</div>

<div class="abs quote"></div>
<div class="abs quote-mark">“</div>
<p class="abs quote-text">We can’t open another Brambles, but we can offer you this collection of our recipes for you to try out at home with your family and friends.</p>

<footer class="abs site-footer">Copyright 2022. Mara Ellison | All Rights Reserved</footer>

</body>
</html>
```